Nine Phase Ledger Roadmap Talk

I would like a flyer to hand out to participants at the speeches that we give. We are a CPA firm that specializes in entrepreneurs and realtors. We would like a flyer that looks crisp and clean, that integrates our logo and our company colors (shades of blue & gold). We would like the wording to be as laid out in the attached documents, but design is up to you. We would like a picture to go along with each point and are open to ideas. The flyer should be one page, preferably just the front.

Colors
3176b5
fee18a

Requirements
Must have
• Our logo and the wording supplied.
• A picture to go along with each topic.
Nice to have
• Images that pop, clean look, professional.
Should not have
• Look messy.

```html
<!DOCTYPE html>
<html lang="en">
<head>
<meta charset="utf-8">
<title>Nine Phase Ledger Roadmap Talk – Agenda</title>
<link href="https://fonts.googleapis.com/css2?family=Montserrat:ital,wght@0,400;0,600;0,800;1,600&family=Open+Sans:ital,wght@0,400;0,600;1,400&display=swap" rel="stylesheet">
<style>
  :root{
    --navy:#1b2839;
    --navy-deep:#142030;
    --navy-soft:#24364d;
    --blue:#3176b5;
    --blue-light:#6cb0e6;
    --gold:#fee18a;
    --ink:#d9e3ee;
    --white:#ffffff;
  }
  *{margin:0;padding:0;box-sizing:border-box}
  html,body{width:896px;height:1200px;overflow:hidden;background:var(--navy-deep)}
  .flyer{
    position:relative;width:896px;height:1200px;overflow:hidden;
    background:linear-gradient(180deg,var(--navy-soft) 0%,var(--navy) 35%,var(--navy-deep) 100%);
    font-family:"Open Sans",Arial,sans-serif;color:var(--ink);
  }
  /* header */
  .brand{position:absolute;left:60px;top:70px;width:330px;text-align:center}
  .brand-name{display:flex;align-items:center;justify-content:center;gap:12px;
    font-family:"Montserrat",Arial,sans-serif;font-weight:800;font-size:34px;letter-spacing:2px;color:var(--blue-light)}
  .brand-mark{width:16px;height:16px;background:var(--gold)}
  .brand-tag{margin-top:6px;font-style:italic;font-size:15px;color:var(--white)}
  .title-divider{position:absolute;left:448px;top:60px;width:2px;height:150px;background:var(--blue-light);opacity:.6}
  .title{position:absolute;left:478px;top:52px;width:380px;font-family:"Montserrat",Arial,sans-serif;color:var(--white);line-height:1}
  .title-lead{font-weight:800;font-size:58px;letter-spacing:-1px}
  .title-lead span{color:var(--gold)}
  .title-sub{margin-top:8px;font-weight:600;font-size:27px;letter-spacing:1px;color:var(--blue-light)}
  .title-agenda{margin-top:6px;font-weight:800;font-size:40px;letter-spacing:3px}
  /* timeline */
  .timeline-path{position:absolute;left:0;top:0}
  .step-text{position:absolute;width:310px;font-size:14px;line-height:1.5;color:var(--ink)}
  .step-text.left{left:62px;text-align:left}
  .step-text.right{left:534px}
  .step-icon{position:absolute;width:62px;height:62px;border-radius:50%;background:var(--white);
    border:3px solid var(--blue-light);display:flex;align-items:center;justify-content:center}
  .step-icon svg{width:32px;height:32px}
  /* closing */
  .tagline{position:absolute;left:0;top:900px;width:896px;text-align:center;
    font-family:"Montserrat",Arial,sans-serif;font-style:italic;font-weight:600;font-size:25px;color:var(--white)}
  .footer{position:absolute;left:0;top:960px;width:896px;height:240px;background:var(--navy-deep);border-top:4px solid var(--blue)}
  .footer-name{margin-top:34px;text-align:center;font-family:"Montserrat",Arial,sans-serif;font-weight:800;font-size:20px;letter-spacing:2px;color:var(--blue-light)}
  .footer-name span{font-weight:400;color:var(--white);letter-spacing:0;font-size:17px}
  .footer-address{margin-top:8px;text-align:center;font-size:14px;color:var(--ink)}
  .contact-bar{position:absolute;left:0;bottom:0;width:896px;height:78px;background:var(--blue);
    display:flex;align-items:center;justify-content:center;gap:42px;font-size:14px;color:var(--white)}
  .contact-item{display:flex;align-items:center;gap:8px}
  .contact-item svg{width:16px;height:16px}
</style>
</head>
<body>
<div class="flyer">

  <header>
    <div class="brand">
      <div class="brand-name"><span class="brand-mark"></span>HARBOR SUMS</div>
      <div class="brand-tag">A Professional Accounting Corporation</div>
    </div>
    <div class="title-divider"></div>
    <h1 class="title">
      <div class="title-lead"><span>NINE</span> PHASE</div>
      <div class="title-sub">LEDGER ROADMAP TALK</div>
      <div class="title-agenda">AGENDA</div>
    </h1>
  </header>

  <svg class="timeline-path" width="896" height="900" viewBox="0 0 896 900" aria-hidden="true">
    <path d="M448 225 C448 260 425 270 425 311 L471 391 L425 471 L471 551 L425 631 L471 711 L425 791 C425 830 448 850 448 880"
          fill="none" stroke="#6cb0e6" stroke-width="3"/>
    <g stroke="#6cb0e6" stroke-width="2">
      <line x1="380" y1="311" x2="394" y2="311"/>
      <line x1="502" y1="391" x2="520" y2="391"/>
      <line x1="380" y1="471" x2="394" y2="471"/>
      <line x1="502" y1="551" x2="520" y2="551"/>
      <line x1="380" y1="631" x2="394" y2="631"/>
      <line x1="502" y1="711" x2="520" y2="711"/>
      <line x1="380" y1="791" x2="394" y2="791"/>
    </g>
  </svg>

  <!-- step 1 -->
  <p class="step-text left" style="top:268px">We will first show you how to reduce your self-employment tax by converting your business into an S Corporation, which can save an owner thousands of dollars each year.</p>
  <div class="step-icon" style="left:394px;top:280px">
    <svg viewBox="0 0 32 32"><circle cx="16" cy="16" r="13" fill="none" stroke="#1b2839" stroke-width="2.5"/><text x="16" y="22" text-anchor="middle" font-family="Montserrat,Arial,sans-serif" font-weight="800" font-size="17" fill="#1b2839">$</text></svg>
  </div>

  <!-- step 2 -->
  <p class="step-text right" style="top:348px">We will show you how to get tax-free income from your corporation by renting your home to the business for board meetings, often worth several thousand dollars a year.</p>
  <div class="step-icon" style="left:440px;top:360px">
    <svg viewBox="0 0 32 32"><path d="M4 16 L16 5 L28 16" fill="none" stroke="#1b2839" stroke-width="2.5" stroke-linejoin="round"/><path d="M8 14 V27 H24 V14" fill="none" stroke="#1b2839" stroke-width="2.5"/><rect x="14" y="19" width="5" height="8" fill="#1b2839"/></svg>
  </div>

  <!-- step 3 -->
  <p class="step-text left" style="top:426px">We will show you the easiest way to track your expenses so that the only thing you will have to do is keep your receipts, and keeping them will be painless.</p>
  <div class="step-icon" style="left:394px;top:440px">
    <svg viewBox="0 0 32 32"><path d="M8 4 H24 V28 L20 25 L16 28 L12 25 L8 28 Z" fill="none" stroke="#1b2839" stroke-width="2.5" stroke-linejoin="round"/><line x1="12" y1="11" x2="20" y2="11" stroke="#1b2839" stroke-width="2"/><line x1="12" y1="16" x2="20" y2="16" stroke="#1b2839" stroke-width="2"/></svg>
  </div>

  <!-- step 4 -->
  <p class="step-text right" style="top:508px">Next, we show you the importance of tax planning and why it is critical to meet with your CPA before the end of the year, not just when you file.</p>
  <div class="step-icon" style="left:440px;top:520px">
    <svg viewBox="0 0 32 32"><rect x="5" y="7" width="22" height="20" rx="2" fill="none" stroke="#1b2839" stroke-width="2.5"/><line x1="5" y1="13" x2="27" y2="13" stroke="#1b2839" stroke-width="2.5"/><line x1="11" y1="4" x2="11" y2="9" stroke="#1b2839" stroke-width="2.5"/><line x1="21" y1="4" x2="21" y2="9" stroke="#1b2839" stroke-width="2.5"/><path d="M11 20 L15 23 L21 17" fill="none" stroke="#1b2839" stroke-width="2.5"/></svg>
  </div>

  <!-- step 5 -->
  <p class="step-text left" style="top:586px">We will show you how to hire your children and pay them a fair wage that is tax-free, moving income to them at a lower rate while you deduct it.</p>
  <div class="step-icon" style="left:394px;top:600px">
    <svg viewBox="0 0 32 32"><circle cx="12" cy="11" r="4.5" fill="#1b2839"/><path d="M4 27 C4 19 20 19 20 27 Z" fill="#1b2839"/><circle cx="23" cy="14" r="3.5" fill="#1b2839"/><path d="M18 27 C18 21 29 21 29 27 Z" fill="#1b2839"/></svg>
  </div>

  <!-- step 6 -->
  <p class="step-text right" style="top:668px">We will discuss how to make your child's college education tax deductible, with savings that can add up to a large sum over the years of study.</p>
  <div class="step-icon" style="left:440px;top:680px">
    <svg viewBox="0 0 32 32"><path d="M2 12 L16 6 L30 12 L16 18 Z" fill="#1b2839"/><path d="M8 15 V22 C12 26 20 26 24 22 V15" fill="none" stroke="#1b2839" stroke-width="2.5"/><line x1="28" y1="12" x2="28" y2="21" stroke="#1b2839" stroke-width="2"/></svg>
  </div>

  <!-- step 7 -->
  <p class="step-text left" style="top:748px">Our grand finale is to show you how to set up a retirement plan that lets you put away tens of thousands of dollars a year before tax.</p>
  <div class="step-icon" style="left:394px;top:760px">
    <svg viewBox="0 0 32 32"><rect x="5" y="20" width="5" height="8" fill="#1b2839"/><rect x="13" y="15" width="5" height="13" fill="#1b2839"/><rect x="21" y="10" width="5" height="18" fill="#1b2839"/><path d="M4 15 L12 8 L17 11 L27 3" fill="none" stroke="#3176b5" stroke-width="2.5"/></svg>
  </div>

  <p class="tagline">If they drive by with a machine gun you don't have to stand up.</p>

  <footer class="footer">
    <div class="footer-name">HARBOR SUMS <span>– A Professional Accounting Corporation</span></div>
    <div class="footer-address">412 Alder Row, Suite 8, Brookfield, CA 90210</div>
    <div class="contact-bar">
      <div class="contact-item">
        <svg viewBox="0 0 16 16"><rect x="1" y="3" width="14" height="10" fill="none" stroke="#fff" stroke-width="1.5"/><path d="M1 3 L8 9 L15 3" fill="none" stroke="#fff" stroke-width="1.5"/></svg>
        hello@harborsums.example
      </div>
      <div class="contact-item">
        <svg viewBox="0 0 16 16"><path d="M3 1 L6 1 L7 5 L5 6 C6 8 8 10 10 11 L11 9 L15 10 L15 13 C15 14 14 15 13 15 C6 15 1 10 1 3 C1 2 2 1 3 1 Z" fill="#fff"/></svg>
        (555) 014-2270
      </div>
      <div class="contact-item">
        <svg viewBox="0 0 16 16"><circle cx="8" cy="8" r="6.5" fill="none" stroke="#fff" stroke-width="1.5"/><ellipse cx="8" cy="8" rx="3" ry="6.5" fill="none" stroke="#fff" stroke-width="1.2"/><line x1="1.5" y1="8" x2="14.5" y2="8" stroke="#fff" stroke-width="1.2"/></svg>
        www.harborsums.example
      </div>
    </div>
  </footer>

</div>
</body>
</html>
```